Selfpublisher sucht Buch-/E-Book-Cover
Zielgruppe
Hallo
Ich bin Selfpublisher und schreibe gerade ein Buch mit dem Themeninhalt 'Grübeln Stoppen' und dafür benötige ich ein kreatives Ebook-Cover und Taschenbuchcover.
Aufgabenstellung
Ich habe detaillierte Vorgaben in meinem Template für den Designer vorbereitet.
Ein Stockphoto für die Covererstellung befindet sich ebenfalls im Anhang.

```html
<!DOCTYPE html>
<html lang="de">
<head>
<meta charset="utf-8">
<title>Raus aus der Gedankenschleife – Buchumschlag</title>
<link rel="stylesheet" href="https://fonts.googleapis.com/css2?family=Bitter:wght@400;600;700;800&display=swap">
<style>
  :root {
    --wall-top: #d6ecf6;
    --wall-mid: #a9d3ea;
    --wall-low: #5fa6cf;
    --floor-top: #3c5f8c;
    --floor-low: #1f3558;
    --title-blue: #137a9c;
    --ink: #231f20;
    --white: #ffffff;
    --panel: rgba(255, 255, 255, 0.32);
    --band: rgba(255, 255, 255, 0.42);
    --spine: #4e9fd0;
  }
  * { margin: 0; padding: 0; box-sizing: border-box; }
  html, body { width: 1200px; height: 932px; overflow: hidden; background: #ffffff; }
  .cover {
    position: relative; width: 1200px; height: 932px; overflow: hidden;
    font-family: "Bitter", Georgia, serif; color: var(--ink);
  }
  .scene-photo {
    position: absolute; inset: 0;
    background: linear-gradient(180deg, var(--wall-top) 0%, var(--wall-mid) 40%, var(--wall-low) 78%, var(--floor-top) 79.8%, var(--floor-low) 100%);
  }
  .figure-photo {
    position: absolute; left: 639px; top: 303px; width: 228px; height: 591px; z-index: 2;
    border-radius: 90px 90px 20px 20px;
    background: linear-gradient(180deg, #6a4a3a 0%, #34507a 22%, #2d4a70 50%, #7a4a32 65%, #5b3a28 100%);
  }
  /* Rückseite */
  .back-headline {
    position: absolute; left: 29px; top: 57px; width: 529px; height: 150px;
    background: var(--panel); text-align: center; padding-top: 6px;
    font-weight: 700; line-height: 1.12;
  }
  .back-headline .l1 { font-size: 31px; display: block; letter-spacing: 0.5px; }
  .back-headline .l2 { font-size: 38px; display: block; letter-spacing: 0.5px; }
  .back-headline .l3 { font-size: 30px; display: block; white-space: nowrap; letter-spacing: 0.6px; }
  .back-blurb {
    position: absolute; left: 29px; top: 246px; width: 529px; height: 408px;
    background: var(--panel); text-align: center;
    font-size: 18.5px; line-height: 26.4px; letter-spacing: 0.5px; padding: 9px 0 0; white-space: nowrap;
  }
  .back-blurb p + p { margin-top: 26.4px; }
  .barcode-area { position: absolute; left: 323px; top: 755px; width: 228px; height: 134px; background: var(--white); }
  /* Rücken */
  .spine { position: absolute; left: 579px; top: 0; width: 42px; height: 932px; background: linear-gradient(180deg, rgba(78,159,208,0.45), var(--spine)); }
  .spine-title, .spine-author {
    position: absolute; white-space: nowrap; transform-origin: left top;
    transform: rotate(-90deg); font-weight: 700; line-height: 42px; font-size: 30px;
  }
  .spine-title { left: 579px; top: 602px; color: var(--ink); letter-spacing: 0.8px; }
  .spine-author { left: 579px; top: 838px; color: var(--white); letter-spacing: 0.5px; }
  /* Vorderseite */
  .front-title { position: absolute; left: 672px; top: 40px; width: 500px; color: var(--title-blue); font-weight: 800; }
  .front-title .t1 { display: block; font-size: 60px; line-height: 66px; white-space: nowrap; }
  .front-title .t2, .front-title .t3 { display: block; font-size: 96px; line-height: 88px; white-space: nowrap; letter-spacing: 1px; }
  .subtitle { position: absolute; right: 0; top: 330px; width: 420px; text-align: right; font-weight: 700; font-size: 24.5px; letter-spacing: 0.4px; z-index: 1; }
  .subtitle span { display: block; height: 43.6px; line-height: 43.6px; padding-right: 36px; }
  .subtitle span:nth-child(even) { background: var(--band); }
  .imprint { position: absolute; left: 930px; top: 786px; color: var(--white); font-weight: 700; font-size: 44px; line-height: 1; letter-spacing: -1px; z-index: 3; }
  .front-author { position: absolute; left: 954px; top: 862px; color: var(--white); font-weight: 700; font-size: 29px; line-height: 1; z-index: 3; }
</style>
</head>
<body>
<div class="cover">
  <div class="scene-photo" role="img" aria-label="Hellblaue Wand mit weißen Kreidekringeln über dunkelblauem Kopfsteinpflaster"></div>

  <div class="back-headline">
    <span class="l1">Erfahrungen aus</span>
    <span class="l2">Leben und Praxis</span>
    <span class="l3">helfen Dir Deinen Weg zu finden.</span>
  </div>
  <div class="back-blurb">
    <p>Grübeln ist so eine Sache für sich. Wir Menschen<br>grübeln jeden Tag, die einen mehr und die anderen<br>weniger. Doch leider sind die Mehrgrübler man-<br>chmal in einer Situation, wo Gefühle, Eindrücke<br>und spezielle Ereignisse dazu führen, dass sie aus<br>dem Grübeln nicht mehr herauskommen. Ich<br>selbst bin gelegentlicher Grübler, dabei habe<br>schon so manches nachgedacht und meine<br>Erfahrungen gesammelt wie man dem Grübeln<br>positiver gegenwirken kann.</p>
    <p>In diesem Buch findest Du lösungsorientierte und<br>praxisnahe Ansätze, die Dir helfen sollen Dein<br>Grübeln zu verstehen und in eine andere Richtung<br>zu lenken.</p>
  </div>
  <div class="barcode-area"></div>

  <div class="spine"></div>
  <div class="spine-title">Raus aus der Gedankenschleife</div>
  <div class="spine-author">Jonas Reiter</div>

  <h1 class="front-title">
    <span class="t1">Raus aus der</span>
    <span class="t2">Gedanken</span>
    <span class="t3">Schleife</span>
  </h1>
  <div class="subtitle">
    <span>Bewusst Grübeln</span>
    <span>stoppen,</span>
    <span>schlechte Gedanken</span>
    <span>loswerden und lernen</span>
    <span>die Gedankenschleife</span>
    <span>zu kontrollieren.</span>
  </div>
  <div class="figure-photo" role="img" aria-label="Mann in Jeanshemd sitzt von hinten gesehen auf einem braunen Stuhl"></div>
  <div class="imprint">klarsinn</div>
  <div class="front-author">Jonas Reiter</div>
</div>
</body>
</html>
```